Judicial election website to attract voters

I need a simple one-page web design for a judicial election. I'm going to put up one picture, maybe two. The picture I have needs a little touch-up (whiten teeth for example). I have 3 paragraphs of text. I'd like a "Donate" button that can link to a CoinDrift account. I'd also like a little background design, like the Constitution or something like that. There's a couple other little things but that's the bulk of it.

Target Market(s)

Involved voters and some media

Industry/Entity Type

Legal

Number of Pages Required

1 page

Font styles to use
Sans Serif

Requirements
Must have
• My picture, text, donate button
• Phrase "Remember to vote August 30, 2016!"
Nice to have
• Perhaps a second photo, maybe a short 30 second video of me talking directly to the voters, cool background: Constitution, something judgey.
Should not have
• Not sure ... profanity, I guess.

```html
<!DOCTYPE html>
<html lang="en">
<head>
<meta charset="utf-8">
<title>Civic Ballot</title>
<link rel="stylesheet" href="https://fonts.googleapis.com/css2?family=Questrial&family=Fira+Sans:ital,wght@1,700&display=swap">
<style>
:root{
  --navy:#1c2f6b;
  --red:#c8102e;
  --banner:#2e5591;
  --text:#3a3a3a;
  --muted:#f4f4f4;
  --footer-dark:#3a3a3a;
  --white:#ffffff;
  --player:#111111;
  --track:#333333;
}
*{box-sizing:border-box;margin:0;padding:0}
html,body{width:809px;height:1200px;overflow:hidden;background:var(--white)}
body{font-family:"Questrial",sans-serif;color:var(--text);position:relative}
.site-header,.hero,.video-section,.about,.site-footer,.copyright{position:absolute;left:0;width:809px}

.brand{font-size:23px;letter-spacing:.2px;color:var(--navy);white-space:nowrap;font-weight:400}
.site-header{top:0;height:76px}
.site-header .brand{position:absolute;left:66px;top:23px}

.donate-btn{position:absolute;width:101px;height:31px;background:var(--navy);border-bottom:2px solid var(--red);color:var(--white);font-size:13.5px;display:flex;align-items:center;justify-content:center;gap:7px;text-decoration:none;letter-spacing:.3px}
.site-header .donate-btn{left:641px;top:23px}

.hero{top:76px;height:323px;background:linear-gradient(125deg,#d7dcee 0%,#c9cfe6 40%,#b9bfd8 62%,#c89a5a 78%,#d3a560 100%)}
.hero-photo{position:absolute;inset:0}
.hero-arrow{position:absolute;top:140px}
.hero-arrow.prev{left:22px}
.hero-arrow.next{right:22px}
.hero-banner{position:absolute;left:0;bottom:0;width:809px;height:46px;background:var(--banner);display:flex;align-items:center;justify-content:center;font-family:"Fira Sans",sans-serif;font-style:italic;font-weight:700;font-size:21px;color:var(--white);letter-spacing:.3px}

.section-title{font-size:19px;color:var(--navy);letter-spacing:.2px;font-weight:400}
.section-title span{color:var(--red)}

.video-section{top:399px;height:359px;text-align:center}
.video-section .section-title{margin-top:28px}
.video-intro{font-size:12.5px;line-height:18px;width:480px;margin:10px auto 0;color:#333}
.video-frame{position:absolute;left:231px;top:115px;width:347px;height:209px;border:1px solid #cfcfcf;border-radius:4px;padding:3px;background:var(--white)}
.video-player{position:relative;width:100%;height:100%;border-radius:3px;overflow:hidden;background:var(--player)}
.video-poster{position:absolute;left:0;top:0;width:100%;height:172px;background:radial-gradient(circle at 20% 30%,#c6593f 0%,transparent 35%),radial-gradient(circle at 85% 40%,#a8303f 0%,transparent 35%),linear-gradient(90deg,#7b6a4e,#c4bdb0 30%,#f2f0ea 50%,#c4bdb0 70%,#6e3040)}
.video-play{position:absolute;left:50%;top:86px;transform:translate(-50%,-50%)}
.video-controls{position:absolute;left:0;bottom:0;display:block}

.about{top:758px;height:347px;background:var(--muted)}
.about-photo{position:absolute;left:68px;top:31px;width:218px;height:284px;background:linear-gradient(180deg,#c9ccd0 0%,#b8b4ae 45%,#d9886a 85%,#e08a6a 100%);border:1px solid #dcdcdc}
.about-text{position:absolute;left:321px;top:28px;width:424px}
.about-text .section-title{margin-bottom:9px}
.about-text p{font-size:12.3px;line-height:17.4px;color:#444}
.about-text p+p{margin-top:10px}

.site-footer{top:1105px;height:66px}
.social{position:absolute;left:67px;top:22px;display:flex;gap:10px;list-style:none}
.social li{width:20px;height:20px;border-radius:3px}
.social .friendlio{background:#3b5998}
.social .chirpline{background:#3fb5ea}
.social .linkwork{background:#1a82bf}
.social .circlespace{background:#dd4b39}
.site-footer .brand{position:absolute;left:0;right:0;top:21px;text-align:center;font-size:19px}
.site-footer .donate-btn{left:641px;top:19px}

.copyright{top:1171px;height:29px;background:var(--footer-dark);color:#e6e6e6;font-size:9px;display:flex;align-items:center;justify-content:center;letter-spacing:.2px}
</style>
</head>
<body>

<header class="site-header">
  <div class="brand">CIVIC BALLOT</div>
  <a class="donate-btn" href="#donate" aria-label="Donate via CoinDrift">
    <svg width="16" height="16" viewBox="0 0 16 16" aria-hidden="true"><circle cx="8" cy="8" r="6.5" fill="none" stroke="#fff" stroke-width="1.6"/></svg>
    DONATE
  </a>
</header>

<section class="hero">
  <div class="hero-photo" role="img" aria-label="Hand tapping an electronic election ballot on a touchscreen"></div>
  <svg class="hero-arrow prev" width="22" height="42" viewBox="0 0 22 42" aria-hidden="true"><path d="M20 1 L2 21 L20 41" fill="none" stroke="#fff" stroke-width="1.5"/></svg>
  <svg class="hero-arrow next" width="22" height="42" viewBox="0 0 22 42" aria-hidden="true"><path d="M2 1 L20 21 L2 41" fill="none" stroke="#fff" stroke-width="1.5"/></svg>
  <div class="hero-banner">REMEMBER TO VOTE AUGUST 30, 2016!</div>
</section>

<section class="video-section">
  <h2 class="section-title">WATCH MY <span>VIDEO</span></h2>
  <p class="video-intro">Lorem ipsum dolor sit amet consectetuer adipiscing elit, sed diam nonummy nibh euismod tincidunt ut laoreet dolore magna aliquam erat volutpat.</p>
  <div class="video-frame">
    <div class="video-player">
      <div class="video-poster" role="img" aria-label="Video still of hands holding an Elections 2016 sign"></div>
      <svg class="video-play" width="32" height="32" viewBox="0 0 32 32" aria-hidden="true"><circle cx="16" cy="16" r="15" fill="#fff" stroke="#ddd"/><path d="M13 9.5 L23 16 L13 22.5 Z" fill="#111"/></svg>
      <svg class="video-controls" width="339" height="29" viewBox="0 0 339 29" aria-hidden="true">
        <rect width="339" height="29" fill="#111"/>
        <rect width="30" height="29" fill="#222"/>
        <path d="M12 9.5 L20 14.5 L12 19.5 Z" fill="#fff"/>
        <text x="38" y="18" fill="#fff" font-size="9.5" font-family="Questrial,sans-serif">04:59</text>
        <rect x="70" y="9" width="188" height="11" rx="5.5" fill="#333"/>
        <rect x="70" y="9" width="67" height="11" rx="5.5" fill="#d0101e"/>
        <circle cx="137" cy="14.5" r="6" fill="#fff"/>
        <text x="266" y="18" fill="#fff" font-size="9.5" font-family="Questrial,sans-serif">10:35</text>
        <path d="M298 12 H301 L305 8.5 V20.5 L301 17 H298 Z" fill="#fff"/>
        <path d="M308 11 Q311 14.5 308 18" fill="none" stroke="#fff" stroke-width="1.3"/>
        <path d="M318 8 L324 14 M318 8 H322 M318 8 V12 M332 22 L326 16 M332 22 H328 M332 22 V18" fill="none" stroke="#fff" stroke-width="1.6"/>
      </svg>
    </div>
  </div>
</section>

<section class="about">
  <div class="about-photo" role="img" aria-label="Portrait photo of the candidate"></div>
  <div class="about-text">
    <h2 class="section-title">ABOUT <span>ME</span></h2>
    <p>Lorem ipsum dolor sit amet, consectetuer adipiscing elit, sed diam nonum nibh euismod tincidunt ut laoreet dolore magna aliquam erat volutpat. Ut wisi enim ad minim veniam, quis nostrud exerci tation ullamcorper suscipit lobortis nisl ut aliquip ex ea commodo consequat.</p>
    <p>Lorem ipsum dolor sit amet, consectetuer adipiscing elit, sed diam nonum nibh euismod tincidunt ut laoreet dolore magna aliquam erat volutpat. Ut wisi enim ad minim veniam, quis nostrud exerci tation ullamcorper suscipit lobortis nisl ut aliquip ex ea commodo consequat.</p>
    <p>Lorem ipsum dolor sit amet, consectetuer adipiscing elit, sed diam nonum nibh euismod tincidunt ut laoreet dolore magna aliquam erat volutpat. Ut wisi enim ad minim veniam, quis nostrud exerci tation ullamcorper suscipit lobortis nisl ut aliquip ex ea commodo consequat Lorem ipsum dolor sit amet, consectetuer adipiscing elit, sed diam nonum.</p>
  </div>
</section>

<footer class="site-footer">
  <ul class="social">
    <li class="friendlio" aria-label="Friendlio"></li>
    <li class="chirpline" aria-label="Chirpline"></li>
    <li class="linkwork" aria-label="Linkwork"></li>
    <li class="circlespace" aria-label="Circlespace"></li>
  </ul>
  <div class="brand">CIVIC BALLOT</div>
  <a class="donate-btn" href="#donate" aria-label="Donate via CoinDrift">
    <svg width="16" height="16" viewBox="0 0 16 16" aria-hidden="true"><circle cx="8" cy="8" r="6.5" fill="none" stroke="#fff" stroke-width="1.6"/></svg>
    DONATE
  </a>
</footer>

<div class="copyright">COPYRIGHT © 2016 CIVIC BALLOT. ALL RIGHTS RESERVED.</div>

</body>
</html>
```